Home Staging Company needs business card design

We're a home staging company called Brightly Settled Home Staging. We would like a business card design that includes aqua and gray. Our current logo of house within chair is fine but I find we almost always use the logo in one color. I'll upload images of front and back of our current card and our logo. Note that we have dropped "Solutions" from our company name and don't want to include it on the card.

Target Market(s)

Realtors and homeowners - people interested in selling their homes

Contact Information for Business Card

Marisol Thistlewood
Brightly Settled Home Staging
757-555-0193
www.brightlysettled.com
marisol@brightlysettled.com

Font styles to use
Serif
Script

Requirements
Must have
• My logo and contact details
• UPDATE***
• I forgot to say that the company name should be included on the front of the card somehow.

```html
<!DOCTYPE html>
<html lang="en">
<head>
<meta charset="utf-8">
<title>Brightly Settled Home Staging – Business Card</title>
<link rel="stylesheet" href="https://fonts.googleapis.com/css2?family=Playfair+Display:wght@400&family=Mulish:wght@400&family=Roboto+Condensed:wght@400&display=swap">
<style>
  :root {
    --backdrop: #b9b9b9;
    --aqua-top: #4fb4bd;
    --aqua-bottom: #1a88b0;
    --aqua: #4ea9b3;
    --charcoal: #33363b;
    --ink: #2b2b2b;
    --paper-top: #f7f7f7;
    --paper-bottom: #e9e9e9;
    --white: #ffffff;
  }
  * { box-sizing: border-box; margin: 0; padding: 0; }
  html, body {
    width: 1200px; height: 576px; overflow: hidden;
    background: var(--backdrop);
  }
  .stage { position: relative; width: 1200px; height: 576px; }
  .card {
    position: absolute; top: 138px;
    width: 484px; height: 293px;
    border-radius: 14px; overflow: hidden;
    box-shadow: 0 3px 6px rgba(0,0,0,0.25);
  }

  /* Front */
  .card-front {
    left: 82px;
    background: linear-gradient(180deg, var(--aqua-top) 0%, var(--aqua-bottom) 100%);
    color: var(--white);
    text-align: center;
  }
  .front-name {
    position: absolute; left: 0; right: 0; top: 96px;
    font-family: "Playfair Display", Georgia, serif;
    font-size: 40px; line-height: 1;
  }
  .front-tagline {
    position: absolute; left: 0; right: 0; top: 160px;
    font-family: "Playfair Display", Georgia, serif;
    font-size: 16px; letter-spacing: 9px;
  }
  .front-web {
    position: absolute; left: 0; right: 0; top: 263px;
    font-family: "Mulish", Arial, sans-serif;
    font-size: 13px;
  }

  /* Back */
  .card-back {
    left: 602px;
    background: linear-gradient(180deg, var(--paper-top) 0%, var(--paper-bottom) 100%);
  }
  .brand { position: absolute; left: 22px; top: 24px; display: flex; align-items: center; gap: 14px; }
  .brand-dot { width: 56px; height: 56px; border-radius: 50%; background: var(--aqua); }
  .brand-name {
    font-family: "Playfair Display", Georgia, serif;
    font-size: 28px; line-height: 1; color: var(--charcoal);
  }
  .brand-tagline {
    font-family: "Playfair Display", Georgia, serif;
    font-size: 11px; letter-spacing: 5px; color: var(--charcoal);
    margin-top: 7px;
  }
  .person { position: absolute; left: 29px; top: 145px; }
  .person-name {
    font-family: "Roboto Condensed", Arial, sans-serif;
    font-size: 20px; color: var(--ink);
  }
  .person-name .surname { color: var(--aqua); }
  .person-title {
    font-family: "Mulish", Arial, sans-serif;
    font-size: 11px; color: var(--ink); margin-top: 4px;
  }
  .wave { position: absolute; left: 0; top: 0; }
  .contacts {
    position: absolute; right: 22px; top: 214px;
    list-style: none; text-align: right;
    font-family: "Mulish", Arial, sans-serif;
    font-size: 12px; color: var(--white);
  }
  .contacts li { display: flex; justify-content: flex-end; align-items: center; gap: 6px; height: 17px; }
  .contacts svg { width: 10px; height: 10px; }
</style>
</head>
<body>
<main class="stage">

  <section class="card card-front" aria-label="Card front">
    <div class="front-name">Brightly Settled</div>
    <div class="front-tagline">HOME STAGING</div>
    <div class="front-web">www.brightlysettled.com</div>
  </section>

  <section class="card card-back" aria-label="Card back">
    <svg class="wave" width="484" height="293" viewBox="0 0 484 293" aria-hidden="true">
      <path fill="var(--aqua)" d="M0 244 C80 272 200 264 280 226 C350 193 420 180 484 184 V293 H0 Z"/>
      <path fill="var(--charcoal)" d="M0 214 C60 238 180 244 262 204 C332 170 410 150 484 156 V168 C410 164 332 186 272 218 C190 260 70 250 0 224 Z"/>
    </svg>

    <div class="brand">
      <span class="brand-dot" aria-hidden="true"></span>
      <div>
        <div class="brand-name">Brightly Settled</div>
        <div class="brand-tagline">HOME STAGING</div>
      </div>
    </div>

    <div class="person">
      <div class="person-name">Marisol <span class="surname">Thistlewood</span></div>
      <div class="person-title">Managing Director</div>
    </div>

    <ul class="contacts">
      <li>757-555-0193
        <svg viewBox="0 0 10 10" aria-hidden="true"><path fill="#fff" d="M1 3 C1 1.5 9 1.5 9 3 V4 H7 V3 H3 V4 H1 Z M2.5 5 H7.5 L8.5 9 H1.5 Z"/></svg>
      </li>
      <li>www.brightlysettled.com
        <svg viewBox="0 0 10 10" aria-hidden="true"><g fill="none" stroke="#fff" stroke-width="1"><circle cx="5" cy="5" r="4"/><ellipse cx="5" cy="5" rx="1.8" ry="4"/><path d="M1 5 H9"/></g></svg>
      </li>
      <li>marisol@brightlysettled.com
        <svg viewBox="0 0 10 10" aria-hidden="true"><rect x="0.5" y="2" width="9" height="6" fill="#fff"/><path d="M0.5 2 L5 5.5 L9.5 2" fill="none" stroke="var(--aqua)" stroke-width="0.8"/></svg>
      </li>
    </ul>
  </section>

</main>
</body>
</html>
```